Robotic Physical Therapy office needs a Grand Opening Flyer

We need a Grand Opening flyer design for a robotic physical therapy office named Kinetic Harbor Wellness. We would like it to have a clean, classy, upscale feeling that gives potential clients a V.I.P. feeling. We would like to use the colors black, gray, and yellow (logo will be uploaded).

Event: Thursday, June 1st, 2023 from 12pm-6pm
location: 58274 Pellham Ave, Bloomfield Hills, MI 48519

Industry/Entity Type

Physical therapy

Font styles to use
Script

Colors

Designer to choose colors to be used in the design.

Requirements
Nice to have
• More of a vip feel for the invite

```html
<!DOCTYPE html>
<html lang="en">
<head>
<meta charset="utf-8">
<title>Kinetic Harbor Wellness – Grand Opening</title>
<link href="https://fonts.googleapis.com/css2?family=Bodoni+Moda:wght@400;500&family=Cinzel:wght@700&display=swap" rel="stylesheet">
<style>
  :root {
    --ink: #050505;
    --ink-soft: #1b1b1b;
    --gold: #f5d82e;
    --gold-faint: rgba(245, 216, 46, 0.22);
    --paper: #ffffff;
  }
  * { margin: 0; padding: 0; box-sizing: border-box; }
  html, body { width: 849px; height: 1200px; overflow: hidden; background: var(--ink); }
  .flyer {
    position: relative;
    width: 849px;
    height: 1200px;
    overflow: hidden;
    background: radial-gradient(ellipse 60% 50% at 50% 40%, var(--ink-soft) 0%, var(--ink) 100%);
    font-family: "Bodoni Moda", "Times New Roman", serif;
    color: var(--paper);
  }
  .frame { position: absolute; inset: 0; }
  .corner-ornament {
    position: absolute;
    width: 130px;
    height: 130px;
  }
  .corner-ornament.top-left { left: 36px; top: 40px; background: radial-gradient(circle at 20% 20%, var(--gold-faint), transparent 70%); }
  .corner-ornament.top-right { right: 36px; top: 40px; background: radial-gradient(circle at 80% 20%, var(--gold-faint), transparent 70%); }
  .corner-ornament.bottom-left { left: 36px; bottom: 40px; background: radial-gradient(circle at 20% 80%, var(--gold-faint), transparent 70%); }
  .corner-ornament.bottom-right { right: 36px; bottom: 40px; background: radial-gradient(circle at 80% 80%, var(--gold-faint), transparent 70%); }

  .brand {
    position: absolute;
    left: 0; right: 0;
    top: 108px;
    display: flex;
    justify-content: center;
    align-items: center;
    gap: 16px;
  }
  .brand-mark {
    width: 64px; height: 64px;
    border-radius: 50%;
    border: 4px solid var(--gold);
  }
  .brand-name {
    font-family: "Cinzel", "Times New Roman", serif;
    font-weight: 700;
    color: var(--gold);
    line-height: 1.02;
  }
  .brand-name .line-main { display: block; font-size: 34px; letter-spacing: 0.5px; }
  .brand-name .line-sub { display: block; font-size: 27px; letter-spacing: 6px; }

  .headline-flourish {
    position: absolute;
    left: 250px; top: 256px;
    width: 350px; height: 358px;
    background: radial-gradient(ellipse at 50% 50%, rgba(245, 216, 46, 0.14) 0%, transparent 68%);
  }
  .headline {
    position: absolute;
    left: 0; right: 0;
    top: 368px;
    text-align: center;
    font-family: "Cinzel", "Times New Roman", serif;
    font-weight: 700;
    color: var(--gold);
    line-height: 1;
  }
  .headline .word-grand { display: block; font-size: 64px; letter-spacing: 1px; }
  .headline .word-opening { display: block; font-size: 66px; margin-top: -3px; letter-spacing: 1px; }

  .divider-ornament {
    position: absolute;
    left: 340px;
    width: 170px;
    height: 24px;
    background: linear-gradient(90deg, transparent, var(--gold-faint), rgba(245,216,46,0.4), var(--gold-faint), transparent);
    border-radius: 12px;
  }
  .divider-ornament.upper { top: 696px; }
  .divider-ornament.lower { top: 974px; }
  .divider-ornament.footer { left: 308px; width: 233px; top: 1090px; height: 34px; }

  .event-date {
    position: absolute;
    left: 0; right: 0;
    top: 766px;
    text-align: center;
    font-size: 35px;
    letter-spacing: 1px;
    white-space: pre;
  }
  .event-date .sep { display: inline-block; margin: 0 30px; }
  .event-time {
    position: absolute;
    left: 0; right: 0;
    top: 834px;
    text-align: center;
    font-size: 29px;
    white-space: pre;
  }
  .event-address {
    position: absolute;
    left: 0; right: 0;
    top: 905px;
    text-align: center;
    font-size: 22px;
    letter-spacing: 0.5px;
  }
</style>
</head>
<body>
<main class="flyer">
  <svg class="frame" width="849" height="1200" viewBox="0 0 849 1200" aria-hidden="true">
    <g stroke="#f5d82e" stroke-width="2.2" fill="none">
      <line x1="174" y1="54" x2="675" y2="54"/>
      <line x1="174" y1="1146" x2="675" y2="1146"/>
      <line x1="49" y1="180" x2="49" y2="1020"/>
      <line x1="800" y1="180" x2="800" y2="1020"/>
      <line x1="239" y1="1132" x2="611" y2="1132" stroke-width="1.6"/>
    </g>
  </svg>

  <div class="corner-ornament top-left" role="img" aria-label="Gold filigree corner ornament"></div>
  <div class="corner-ornament top-right" role="img" aria-label="Gold filigree corner ornament"></div>
  <div class="corner-ornament bottom-left" role="img" aria-label="Gold filigree corner ornament"></div>
  <div class="corner-ornament bottom-right" role="img" aria-label="Gold filigree corner ornament"></div>

  <header class="brand">
    <span class="brand-mark" aria-hidden="true"></span>
    <h2 class="brand-name">
      <span class="line-main">KINETIC HARBOR</span>
      <span class="line-sub">WELLNESS</span>
    </h2>
  </header>

  <div class="headline-flourish" role="img" aria-label="Gold calligraphic swirls and sparkles framing the headline"></div>
  <h1 class="headline">
    <span class="word-grand">GRAND</span>
    <span class="word-opening">OPENING</span>
  </h1>

  <div class="divider-ornament upper" role="img" aria-label="Small gold scroll divider"></div>

  <p class="event-date">THURSDAY<span class="sep">|</span>1st  JUNE<span class="sep">|</span>2023</p>
  <p class="event-time">12:00 pm   -   6:00 pm</p>
  <p class="event-address">58274 Pellham Ave, Bloomfield Hills, MI 48519</p>

  <div class="divider-ornament lower" role="img" aria-label="Small gold scroll divider"></div>
  <div class="divider-ornament footer" role="img" aria-label="Gold scroll ornament above the base rule"></div>
</main>
</body>
</html>
```